Harwick + Pell Architect Marketing campaign for a morern fresh architecture cutting egde firm th...

To create en exciting template for our monthly newsletters to go out to all our clients via email. I have added a bit of an idea of what we like but not limited to..... we like a nice clean fresh look with lots of white space. I hve aslo added a sketch of the type of how we might layt it out - you may have a better idea. also the pics of the projects for the first issue (issue #1)We like the opening page like the attached brewlane had and replace the cup with apic of our building/office. Cant wait to see what you come up with.

Target Market(s)

young professionals

Industry/Entity Type

Architectural

Font styles to use
Serif

Colors

Designer to choose colors to be used in the design.

Requirements
Must have
• Logo, text information provided, photos provided
Nice to have
• lots of white space, clean and frest looking

```html
<!DOCTYPE html>
<html lang="en">
<head>
<meta charset="utf-8">
<title>Harwick + Pell Architecture — Newsletter Issue #1</title>
<link href="https://fonts.googleapis.com/css2?family=Poppins:wght@300;400;500;600&display=swap" rel="stylesheet">
<style>
:root{
  --ink:#111111;
  --text:#2a2a2a;
  --muted:#8a8a8a;
  --rule:#d6d6d6;
  --paper:#ffffff;
  --mist:#efefef;
  --night:#2b2b2b;
  --social-blue:#3b5998;
  --social-sky:#1da1f2;
  --social-red:#bd081c;
  --social-orange:#dd4b39;
}
*{margin:0;padding:0;box-sizing:border-box}
html,body{width:1200px;height:5004px;overflow:hidden}
body{font-family:"Poppins",sans-serif;color:var(--text);background:var(--paper);position:relative}
.abs{position:absolute}

/* top bar */
.top-bar{position:absolute;left:0;top:0;width:1200px;height:171px;background:var(--paper)}
.view-online{left:74px;top:30px;font-size:28px;color:var(--muted);font-weight:300}
.social-top{left:880px;top:24px;display:flex;gap:18px}
.social-top span{width:46px;height:46px;border-radius:50%;display:block}
.top-rule{left:74px;top:93px;width:1050px;height:1px;background:var(--rule)}
.contact-row{top:112px;font-size:28px;color:var(--muted);font-weight:300;display:flex;align-items:center;gap:12px}
.contact-row svg{width:26px;height:26px}

/* header */
.site-header{position:absolute;left:0;top:171px;width:1200px;height:159px;background:var(--paper)}
.brand{left:85px;top:6px;width:124px;height:140px}
.brand-box{position:absolute;left:0;top:0;width:124px;height:110px;border:8px solid var(--ink)}
.brand-name{position:absolute;left:0;top:118px;width:124px;font-size:11px;font-weight:600;color:var(--ink);text-align:center;letter-spacing:1px;white-space:nowrap}
.nav{top:56px;font-size:29px;color:var(--text);font-weight:400}

/* hero */
.hero{position:absolute;left:0;top:330px;width:1200px;height:750px;
  background:linear-gradient(180deg,#3c4a6e 0%,#6a7a9c 30%,#8a8a92 45%,#3a3632 62%,#2a2622 80%,#4a4640 100%)}
.hero-card{left:74px;top:202px;width:700px;height:548px;background:rgba(15,15,15,.72);border-left:26px solid #050505;border-top:26px solid #050505}
.hero-title{left:160px;top:256px;font-size:40px;font-weight:500;color:#fff}
.hero-text{left:160px;top:318px;width:575px;font-size:23px;line-height:45px;color:#f2f2f2;font-weight:300;text-align:justify}

/* section headings */
.section-title{font-size:37px;font-weight:500;color:var(--ink);padding-left:26px;line-height:56px;white-space:nowrap}
.section-title::before{content:"";position:absolute;left:0;top:-2px;width:64px;height:62px;border:6px solid var(--ink);border-right:none}
.project-tag{font-size:23px;color:var(--ink);font-weight:500}
.project-tag em{font-style:normal;font-weight:400}
.body-copy{font-size:23px;line-height:45px;text-align:justify;font-weight:300;color:var(--text)}

/* sections */
.band{position:absolute;left:0;width:1200px}
.band-mist{background:var(--mist)}

/* image frames */
.frame{position:absolute;background:#0a0a0a}
.frame .photo{position:absolute}

/* footer */
.footer{position:absolute;left:0;top:4437px;width:1200px;height:567px;background:var(--night);color:#fff;text-align:center}
.footer-title{top:78px;left:0;width:1200px;font-size:40px;font-weight:500}
.footer-text{top:124px;left:140px;width:920px;font-size:23px;line-height:44px;font-weight:300}
.footer-social{left:505px;top:220px;display:flex;gap:14px}
.footer-social span{width:54px;height:54px;border-radius:50%;border:2px solid #fff;display:block}
.badge{position:absolute}
.copyright{top:4958px;left:0;width:1200px;text-align:center;font-size:20px;color:#fff;font-weight:300}
.issue-code{top:4958px;left:1138px;font-size:20px;color:#fff;font-weight:300}
</style>
</head>
<body>

<header class="top-bar">
  <div class="abs view-online">View Online Version</div>
  <div class="abs social-top" aria-label="Social links">
    <span style="background:var(--social-blue)"></span>
    <span style="background:var(--social-sky)"></span>
    <span style="background:var(--social-red)"></span>
    <span style="background:var(--social-orange)"></span>
  </div>
  <div class="abs top-rule"></div>
  <div class="abs contact-row" style="left:74px">
    <svg viewBox="0 0 24 24"><circle cx="12" cy="12" r="10" fill="#9a9a9a"/><path d="M2 12h20M12 2c3 3 3 17 0 20M12 2c-3 3-3 17 0 20" stroke="#fff" stroke-width="1.5" fill="none"/></svg>
    HarwickPell.com
  </div>
  <div class="abs contact-row" style="left:446px">
    <svg viewBox="0 0 24 24"><rect x="2" y="5" width="20" height="15" rx="2" fill="none" stroke="#9a9a9a" stroke-width="2.5"/><path d="M3 7l9 7 9-7" stroke="#9a9a9a" stroke-width="2" fill="none"/></svg>
    info@harwickpell.com
  </div>
  <div class="abs contact-row" style="left:882px">
    <svg viewBox="0 0 24 24"><path d="M6 2l4 4-2 3c1 3 4 6 7 7l3-2 4 4-3 4C10 22 2 14 2 5z" fill="#9a9a9a"/></svg>
    + 888 888 8888
  </div>
</header>

<div class="site-header">
  <div class="abs brand">
    <div class="brand-box"></div>
    <div class="brand-name">HARWICK + PELL</div>
  </div>
  <div class="abs nav" style="left:586px">Construction</div>
  <div class="abs nav" style="left:808px">About Us</div>
  <div class="abs nav" style="left:973px">Contact Us</div>
</div>

<section class="hero" role="img" aria-label="Dusk photograph of the studio's office building with lit glass frontage">
  <div class="abs hero-card"></div>
  <h1 class="abs hero-title">We’re glad you’re here</h1>
  <p class="abs hero-text">Now that you are a Harwick + Pell Architecture insider you’ll be among the first to hear about upcoming projects that the studio is working on, completed projects, news and more.</p>
</section>

<section class="band band-mist" style="top:1080px;height:415px">
  <h2 class="abs section-title" style="left:482px;top:66px">WELCOME</h2>
  <p class="abs body-copy" style="left:118px;top:148px;width:964px;text-align:center">It appears that there are a lot of people are genuinely interested in the building and construction industry, and we here at Harwick + Pell Architecture often get asked “what we are up to” and “what cool projects have we got on the go”. With that being said we thought we would share with you some of our projects at various stages for you all to enjoy</p>
</section>

<section class="band" style="top:1495px;height:827px">
  <h2 class="abs section-title" style="left:74px;top:93px">ON THE DRAWING BOARD</h2>
  <div class="abs project-tag" style="left:74px;top:172px">LAKE HOOD HOUSE // <em>RESIDENTIA</em></div>
  <p class="abs body-copy" style="left:74px;top:216px;width:526px">We have recently completed this two story house concept overlooking the canals at Lake Hood here in Ashburton. We are currently in the Working Drawing phase at present.</p>
  <p class="abs body-copy" style="left:74px;top:456px;width:526px">This house will stand out from the crowd and has a mixture of cedar, standing seam wall cladding and precast concrete panels. We are really excited to see this project to progress to construction. We will keep you posted on this one!!</p>
  <div class="frame" style="left:621px;top:62px;width:465px;height:348px">
    <div class="photo" role="img" aria-label="Render of a modern building at dusk with curved blue light accents" style="left:42px;top:34px;right:0;bottom:38px;background:linear-gradient(180deg,#5a6890 0%,#7c86a2 45%,#2a2a2c 70%,#3a3630 100%)"></div>
  </div>
  <div class="frame" style="left:621px;top:418px;width:465px;height:348px">
    <div class="photo" role="img" aria-label="Evening view of a low industrial building with lit entrance" style="left:42px;top:0;right:0;bottom:38px;background:linear-gradient(180deg,#4f5c86 0%,#8a93b4 45%,#3a3e44 68%,#55574f 100%)"></div>
  </div>
</section>

<section class="band band-mist" style="top:2322px;height:1041px">
  <h2 class="abs section-title" style="left:596px;top:66px">UNDER CONSTRUCTION</h2>
  <div class="abs project-tag" style="left:596px;top:142px">ALDGATE STREET – STAGE 1 // <em>COMMERCIAL</em></div>
  <p class="abs body-copy" style="left:596px;top:184px;width:526px">This new development currently being construction by Larkfield Commercial in Rolleston is theanchor development for Aldgate Street and the beginning of the reconfiguration / upgrade of the Rolleston Town Centre. This is part of a major redevelopment for Rolleston.</p>
  <p class="abs body-copy" style="left:596px;top:498px;width:526px">We have worked closely with the Westvale District Council and surrounding residential neighbours so that new development benefits all involved. The building is fully tenanted with Monochrome Coffee, Jade Lantern Chinese Restaurant, Saffron House Restaurant, Cellar Corner, Threadline Clothing Store and a small dairy. Tenants are currently completing fit-outs for the spaces and the project is fast nearing completion and will be open for business in the next few months.</p>
  <div class="frame" style="left:105px;top:101px;width:462px;height:348px">
    <div class="photo" role="img" aria-label="Construction site of a two-storey commercial building with scaffolding" style="left:42px;top:38px;right:0;bottom:0;background:linear-gradient(180deg,#c9ccd0 0%,#b8bcc2 40%,#3c3c3e 58%,#5a5a5a 80%,#6e6e6c 100%)"></div>
  </div>
  <div class="frame" style="left:107px;top:558px;width:460px;height:382px">
    <div class="photo" role="img" aria-label="Commercial building with curved copper cladding under construction" style="left:42px;top:38px;right:0;bottom:38px;background:linear-gradient(90deg,#7a4a32 0%,#b57a56 25%,#8a5a40 40%,#4a4a4c 60%,#8c8e92 100%)"></div>
  </div>
</section>

<section class="band" style="top:3363px;height:1074px">
  <h2 class="abs section-title" style="left:74px;top:91px">FEATURE PROJECT</h2>
  <div class="abs project-tag" style="left:74px;top:170px;width:526px;line-height:48px">KEYSTONE CUTTING &amp; PROCESSING LTD // COMMERCIAL</div>
  <p class="abs body-copy" style="left:74px;top:262px;width:526px">This new office and factory located in the new Ashburton Business Park is comprised of a large Cutting and Processing facility for the manufacturer of steel plate profiles. The facility 1,500m² houses two 10-tonne gantry cranes running the full length of the 60 x 25 metre workshop and was designed with the emphasis on maximum plate storage and profile cutting efficiency.</p>
  <p class="abs body-copy" style="left:600px;top:703px;width:524px">Alongside the processing facility is an attached 238m² modern single level office building has been designed to project the character and brand of Keystone Cutting and to sit within the context of the Business Park. The interior fit-out uses a limited palette of materials to create a modern uncluttered interior.</p>
  <div class="frame" style="left:621px;top:171px;width:465px;height:350px">
    <div class="photo" role="img" aria-label="Landscape render of a dark office building beside a water feature and planting" style="left:42px;top:38px;right:0;bottom:36px;background:linear-gradient(180deg,#c2c6c8 0%,#9a9e9c 35%,#5a6a4e 60%,#6a8e9a 80%,#8aa07a 100%)"></div>
  </div>
  <div class="frame" style="left:82px;top:662px;width:465px;height:350px">
    <div class="photo" role="img" aria-label="Render of timber entry steps and garden beside the office" style="left:42px;top:38px;right:0;bottom:36px;background:linear-gradient(135deg,#2a2a2a 0%,#6a5e50 40%,#a08466 55%,#6e8a5a 80%,#c8ccc4 100%)"></div>
  </div>
</section>

<footer class="footer">
  <h2 class="abs footer-title">Stay Connection With Us</h2>
  <p class="abs footer-text">Also remember to follow us on our social media platforms where are keeping our followers up to date frequently.</p>
  <div class="abs footer-social" aria-label="Social links"><span></span><span></span><span></span></div>
  <div class="badge" role="img" aria-label="Professional membership badge" style="left:249px;top:310px;width:227px;height:165px;background:#5c5c5c;border-radius:4px"></div>
  <div class="badge" role="img" aria-label="Industry association badge" style="left:534px;top:316px;width:417px;height:150px;background:#1a3d8a;border-radius:4px"></div>
</footer>
<div class="abs copyright">Copyright © 2019. All Rights Reserved.</div>
<div class="abs issue-code">C29</div>

</body>
</html>
```